Business card design for Automotive workshop

We need a business card for a new automotive repair and tyre shop called Keelstone Prime Automotive located in New Zealand. We are a clean, modern and fresh workshop and company.

Front needs to feature logo,
my name:
Marlo Fenwicke (director)

Address:
48 Tarn Lane
Rangiwhero 3592

Phone: 07 594 2713
Mobile: 027 451 9362
Email: office@keelstoneautomotive.example.nz
Website: keelstoneautomotive.example.nz

Back needs to feature an area to write down appointment details, date and time.

Also feature a list of jobs and work we do such as,
Vehicle Servicing
All Mechanical Repairs
Warrant of Fitness
Tyres & Wheel Alignments
Automotive Diagnostics
Automotive Parts & Supplies

```html
<!DOCTYPE html>
<html lang="en">
<head>
<meta charset="utf-8">
<title>Keelstone Prime Automotive – Business Card</title>
<link rel="stylesheet" href="https://fonts.googleapis.com/css2?family=PT+Sans:wght@400;700&display=swap">
<style>
  :root {
    --stage: #3a3a3a;
    --stage-light: #555555;
    --card-dark: #2b2b2b;
    --brand-red: #e02128;
    --paper: #ffffff;
    --ink: #1c1c1c;
    --fold: #c9c9c9;
  }
  * { box-sizing: border-box; margin: 0; padding: 0; }
  html, body { width: 1200px; height: 750px; overflow: hidden; }
  body {
    background: radial-gradient(ellipse at 50% 45%, var(--stage-light) 0%, var(--stage) 45%, #262626 100%);
    font-family: "PT Sans", sans-serif;
    position: relative;
  }
  .card {
    position: absolute;
    top: 186px;
    width: 560px;
    height: 328px;
    border-radius: 16px;
    overflow: hidden;
    background: var(--card-dark);
    box-shadow: 0 4px 10px rgba(0,0,0,.45);
  }
  .card--front { left: 38px; }
  .card--back { left: 610px; }
  .card__shapes { position: absolute; inset: 0; }

  .brand-name {
    position: absolute;
    color: var(--brand-red);
    font-weight: 700;
    text-transform: uppercase;
    line-height: 1.05;
    text-align: center;
    letter-spacing: 1px;
  }
  .card--front .brand-name { left: 22px; top: 146px; width: 220px; font-size: 22px; }
  .card--back .brand-name { left: 222px; top: 110px; width: 310px; font-size: 31px; }

  .info-strip {
    position: absolute;
    right: 0;
    background: var(--paper);
    color: var(--ink);
    display: flex;
    align-items: center;
    gap: 5px;
    font-size: 16px;
    line-height: 1;
    padding-left: 8px;
    white-space: nowrap;
  }
  .info-strip svg { width: 13px; height: 13px; flex: none; }
  .info-strip--name {
    left: 307px; top: 40px; height: 44px;
    flex-direction: column; align-items: flex-start; justify-content: center;
    padding-left: 26px; gap: 2px;
  }
  .person-name { font-size: 18.5px; font-weight: 700; position: relative; }
  .person-name svg { position: absolute; left: -18px; top: 3px; width: 12px; height: 13px; }
  .person-role { font-size: 14px; }
  .info-strip--address { left: 284px; top: 112px; height: 20px; }
  .info-strip--mobile { left: 263px; top: 162px; height: 20px; }
  .info-strip--phone { left: 248px; top: 200px; height: 20px; }
  .info-strip--email { left: 233px; top: 238px; height: 20px; padding-left: 5px; }
  .info-strip--web { left: 217px; top: 274px; height: 21px; }

  .service-list { list-style: none; position: absolute; left: 19px; top: 0; }
  .service-list li {
    position: absolute;
    left: 0;
    color: var(--paper);
    font-size: 14.5px;
    letter-spacing: .4px;
    white-space: nowrap;
    transform: translateY(-50%);
  }

  .appointment {
    position: absolute;
    left: 278px; top: 280px;
    color: var(--ink);
    font-size: 17px;
    display: flex; gap: 6px;
    white-space: nowrap;
  }
  .appointment__field { display: inline-flex; align-items: flex-end; }
  .appointment__line { display: inline-block; width: 86px; border-bottom: 1px solid var(--ink); margin-bottom: 4px; margin-left: 1px; }
</style>
</head>
<body>

<section class="card card--front" aria-label="Business card front">
  <svg class="card__shapes" viewBox="0 0 560 328" width="560" height="328" aria-hidden="true">
    <polygon points="364,0 560,0 560,328 231,328" fill="var(--brand-red)"/>
    <polygon points="307,84 331,84 313,104" fill="var(--fold)"/>
    <polygon points="284,132 308,132 290,152" fill="var(--fold)"/>
    <polygon points="263,182 287,182 270,200" fill="var(--fold)"/>
    <polygon points="248,220 272,220 255,238" fill="var(--fold)"/>
    <polygon points="233,258 257,258 239,274" fill="var(--fold)"/>
    <polygon points="217,295 241,295 228,318" fill="var(--fold)"/>
  </svg>

  <div class="brand-name">Keelstone Prime<br>Automotive</div>

  <div class="info-strip info-strip--name">
    <span class="person-name">
      <svg viewBox="0 0 12 13" aria-hidden="true"><circle cx="6" cy="3.5" r="3.2" fill="var(--brand-red)"/><path d="M0 13 C0 8 2.5 7 6 7 C9.5 7 12 8 12 13Z" fill="var(--brand-red)"/></svg>
      Marlo Fenwicke
    </span>
    <span class="person-role">Managing Director</span>
  </div>
  <div class="info-strip info-strip--address">48 Tarn Lane.Rangiwhero 3592</div>
  <div class="info-strip info-strip--mobile">
    <svg viewBox="0 0 13 13" aria-hidden="true"><rect x="2" y="0" width="9" height="13" rx="1.5" fill="var(--ink)"/><rect x="3.5" y="1.5" width="6" height="8" fill="var(--paper)"/></svg>
    + 027 451 9362
  </div>
  <div class="info-strip info-strip--phone">
    <svg viewBox="0 0 13 13" aria-hidden="true"><rect x="0" y="0" width="13" height="13" rx="1.5" fill="var(--ink)"/><path d="M2.5 6 Q6.5 2 10.5 6 L9 7 L8 5.5 L5 5.5 L4 7Z M3.5 8 H9.5 V10.5 H3.5Z" fill="var(--paper)"/></svg>
    + 07 594 2713
  </div>
  <div class="info-strip info-strip--email">
    <svg viewBox="0 0 13 13" aria-hidden="true"><rect x="0" y="0" width="13" height="13" rx="1.5" fill="var(--ink)"/><rect x="2" y="3.5" width="9" height="6" fill="var(--paper)"/><path d="M2 3.5 L6.5 7 L11 3.5" stroke="var(--ink)" stroke-width="1" fill="none"/></svg>
    office@keelstoneautomotive.example.nz
  </div>
  <div class="info-strip info-strip--web">
    <svg viewBox="0 0 13 13" aria-hidden="true"><rect x="0" y="0" width="13" height="13" rx="1.5" fill="var(--ink)"/><circle cx="6.5" cy="6.5" r="4" fill="none" stroke="var(--paper)" stroke-width="1"/><path d="M2.5 6.5 H10.5 M6.5 2.5 V10.5" stroke="var(--paper)" stroke-width="1"/></svg>
    keelstoneautomotive.example.nz
  </div>
</section>

<section class="card card--back" aria-label="Business card back">
  <svg class="card__shapes" viewBox="0 0 560 328" width="560" height="328" aria-hidden="true">
    <polygon points="0,0 146,0 278,328 0,328" fill="var(--brand-red)"/>
    <g fill="var(--paper)">
      <polygon points="0,45 12,57 0,69"/>
      <polygon points="0,90 12,102 0,114"/>
      <polygon points="0,134 12,146 0,158"/>
      <polygon points="0,180 12,192 0,204"/>
      <polygon points="0,225 12,237 0,249"/>
      <polygon points="0,270 12,282 0,294"/>
    </g>
    <polygon points="259,271 560,271 560,310 275,310" fill="var(--paper)"/>
  </svg>

  <ul class="service-list">
    <li style="top:57px">Vehicle Servicing</li>
    <li style="top:102px">All Mechanical Repairs</li>
    <li style="top:146px">Warrant of Fitness</li>
    <li style="top:192px">Tyres &amp; Wheel Alignments</li>
    <li style="top:237px">Automotive Diagnostics</li>
    <li style="top:282px">Automotive Parts &amp; Supplies</li>
  </ul>

  <div class="brand-name">Keelstone Prime<br>Automotive</div>

  <div class="appointment">
    <span class="appointment__field">Time<span class="appointment__line"></span></span>
    <span class="appointment__field">Date<span class="appointment__line"></span></span>
  </div>
</section>

</body>
</html>
```